Thank You For Shopping / Hair Care Tips

I need “Thank You For Shopping”
Post cards made for my hair business !
I added pictures of post cards that I really like . I also added my LunaKova Wigs logo for you guys to use

I want the backside of the flyer to have hair care tips !
I want people to have full directions on how to care for their wigs

Target Market(s)

Im marking to young woman to older middle aged woman
Ages 23-66 . I want my flyer to look mature And classy

Industry/Entity Type

Hair And Beauty

Font styles to use
Serif
Script

Colors
e34699
e34298
e34398

Requirements
Must have
• The flyer must have the Instagram logo with my Instagram name next to it @luna.kova.wigs__
• Also it must have my “Luna Kova Wigs” logo that I’ve uploaded in the pictures section .
• Flyer had to be two sides . One side “ thank you for shopping “ side two “hair care tips”
• My website must be on the flyer - www.lunakovawigs.example
• The flyer must match the colors of my logo
• All white . With the pink and glitter sliver you see on my logo
Nice to have
• Nice to have a glitter border
Should not have
• The flyer should not have different colors that don’t match my logo
• It shouldn’t be made without having my Instagram or website on the flyer

```html
<!DOCTYPE html>
<html lang="en">
<head>
<meta charset="utf-8">
<title>Luna Kova Wigs – Thank You and Hair Care Tips Postcards</title>
<link rel="stylesheet" href="https://fonts.googleapis.com/css2?family=Kaushan+Script&family=Questrial&display=swap">
<style>
  :root {
    --pink: #e34699;
    --plum-deep: #1c0812;
    --plum: #3a0d26;
    --plum-glow: #6b1e4c;
    --silver-light: #e4e4e4;
    --silver: #b9b9b9;
    --silver-dark: #8d8d8d;
    --ink: #111111;
    --white: #ffffff;
    --stage: #eeeeee;
    --hair-dark: #3a2a1f;
    --hair-mid: #6b4a33;
  }
  * { box-sizing: border-box; margin: 0; padding: 0; }
  html, body { width: 1200px; height: 800px; overflow: hidden; }
  body { background: var(--stage); position: relative; font-family: "Questrial", sans-serif; }

  .postcard {
    position: absolute;
    top: 207px;
    width: 560px;
    height: 386px;
    overflow: hidden;
    box-shadow: 0 6px 18px rgba(0,0,0,0.18);
  }
  .postcard--front { left: 20px; }
  .postcard--back { left: 620px; background: var(--plum-deep); }

  /* Front */
  .front-art { position: absolute; inset: 0; }
  .hair-sample {
    position: absolute; left: 214px; top: 0; width: 74px; height: 88px;
    border-radius: 0 0 45% 45%;
    background: radial-gradient(circle at 50% 40%, var(--hair-mid), var(--hair-dark));
  }
  .thanks {
    position: absolute; right: 20px; top: 16px; text-align: right;
    font-family: "Kaushan Script", cursive; line-height: 1;
  }
  .thanks__line1 { display: block; color: var(--ink); font-size: 30px; margin-right: 38px; }
  .thanks__line2 { display: block; font-size: 40px; margin-top: 4px; }
  .thanks__for { color: var(--ink); }
  .thanks__shopping { color: var(--pink); }
  .brand-name {
    position: absolute; left: 70px; top: 148px; width: 310px;
    color: var(--pink); font-family: "Questrial", sans-serif;
    font-size: 54px; line-height: 1.05; text-align: center; letter-spacing: 2px;
  }
  .contact { position: absolute; color: var(--white); font-size: 15px; letter-spacing: 0.5px; display: flex; align-items: center; gap: 8px; }
  .contact--web { left: 74px; bottom: 40px; }
  .contact--social { right: 48px; bottom: 66px; }
  .contact__dot { width: 15px; height: 15px; border: 2px solid var(--pink); border-radius: 50%; flex: none; }

  /* Back */
  .back-panel {
    position: absolute; inset: 12px;
    border: 9px solid var(--silver);
    outline: 2px solid var(--silver-dark);
    background: linear-gradient(100deg, var(--plum-deep) 0%, var(--plum) 45%, var(--plum-glow) 80%, var(--plum) 100%);
  }
  .model-portrait {
    position: absolute; right: 10px; top: 22px; width: 140px; height: 322px;
    border-radius: 60px 60px 0 0;
    background: linear-gradient(180deg, var(--hair-dark) 0%, var(--hair-mid) 55%, #c9a27e 100%);
  }
  .tips-title { position: absolute; left: 34px; top: 30px; font-family: "Kaushan Script", cursive; font-size: 44px; line-height: 1; font-weight: 400; }
  .tips-title__pink { color: var(--pink); }
  .tips-title__white { color: var(--white); }
  .tips-intro {
    position: absolute; left: 28px; top: 96px; width: 322px;
    color: var(--white); font-size: 10.5px; line-height: 1.3;
    padding: 4px 6px; background: rgba(255,255,255,0.06);
  }
  .tips-list { position: absolute; left: 34px; top: 140px; width: 320px; list-style: none; color: var(--white); font-size: 11px; line-height: 13px; }
  .tips-list li { margin-bottom: 7px; }
  .tips-follow { position: absolute; left: 34px; bottom: 20px; color: var(--white); font-size: 11px; display: flex; align-items: center; gap: 8px; }
  .tips-follow__handle { color: var(--pink); background: rgba(255,255,255,0.06); padding: 3px 8px; }
</style>
</head>
<body>

<section class="postcard postcard--front" aria-label="Thank you postcard, front">
  <svg class="front-art" width="560" height="386" viewBox="0 0 560 386" aria-hidden="true">
    <defs>
      <linearGradient id="silverFill" x1="0" y1="0" x2="1" y2="1">
        <stop offset="0" stop-color="#cfcfcf"/>
        <stop offset="0.5" stop-color="#efefef"/>
        <stop offset="1" stop-color="#bdbdbd"/>
      </linearGradient>
      <radialGradient id="plumFill" cx="0.3" cy="0.85" r="0.8">
        <stop offset="0" stop-color="#5a1840"/>
        <stop offset="0.6" stop-color="#320b22"/>
        <stop offset="1" stop-color="#1c0812"/>
      </radialGradient>
    </defs>
    <rect width="560" height="386" fill="url(#silverFill)"/>
    <path d="M0 110 C 60 72, 140 56, 220 68 C 320 84, 420 150, 500 156 C 530 158, 550 150, 560 142 L560 386 L0 386 Z" fill="url(#plumFill)"/>
    <path d="M0 110 C 60 72, 140 56, 220 68 C 320 84, 420 150, 500 156 C 530 158, 550 150, 560 142" fill="none" stroke="#e34699" stroke-width="5"/>
  </svg>
  <div class="hair-sample" role="img" aria-label="Photo of a wavy brown wig lock"></div>
  <p class="thanks">
    <span class="thanks__line1">Thank you</span>
    <span class="thanks__line2"><span class="thanks__for">For</span> <span class="thanks__shopping">Shopping</span></span>
  </p>
  <p class="brand-name">Luna Kova Wigs</p>
  <p class="contact contact--web"><span class="contact__dot"></span>LUNAKOVAWIGS.EXAMPLE</p>
  <p class="contact contact--social"><span class="contact__dot"></span>@luna.kova.wigs</p>
</section>

<section class="postcard postcard--back" aria-label="Hair care tips postcard, back">
  <div class="back-panel">
    <div class="model-portrait" role="img" aria-label="Illustration of a woman with long straight brown hair"></div>
    <h1 class="tips-title"><span class="tips-title__pink">Hair Care</span> <span class="tips-title__white">Tips !</span></h1>
    <p class="tips-intro">Congratulations on your purchase of your Primium<br>Here are the few tips to help maintain the quality you want</p>
    <ol class="tips-list">
      <li>1. Apply Warm Oil On The Hair</li>
      <li>2. Use Rice Water As A Shampoo And A Rinse For Hair Care</li>
      <li>3. Eggs Can Contribute To Overall Hair Health</li>
      <li>4. Apply onion juice all over your hair</li>
      <li>5. Use As Much Green Tea On Your Hair As Possible</li>
      <li>6. Use A Beer Rinse Whenever You Can For Hair Care!</li>
      <li>7. Use As Much Green Tea On Your Hair As Possible</li>
    </ol>
    <p class="tips-follow">for More tips follow me on <span class="tips-follow__handle">@luna.kova.wigs</span></p>
  </div>
</section>

</body>
</html>
```